Application page web design and internal pages

Create a web site where home
Page looks like an application screen for a mobile phone

Use bold icons and colors with images that have round edges

PorlenPurse Apps is name of page

Search bar at the top

Use colors from Vextaro.org for background

Price of ZORBS in top right corner (https://www.quelvix.example/trade/en-US?symbol=ZORBS_USDT&layout=basic&theme=dark)

Pages within each app should be the same color as the icon

Use the following as app icons on the page:
Key
Icon name: first screen; second screen (text)

⁃ Balances: enter pin; display balances (Your account can hold multiple currency denominations. Your balances are: ZORBS 1234567890)
⁃ Transactions: enter pin; display transactions (Your last 5 payments are ZORBS 10 from Vextaro)
⁃ Send Money: enter phone number, enter amount, send button; display message
⁃ Create Account: choose country code, enter phone number, create button; enter pin; display message ( (phone number) will be notified when their account has been created)
⁃ My Wallet Address: enter pin; display public key (IMPORTANT Send only STELLAR blockchain tokens to this deposit address: GDXQ7PLM2ZNVA9TRK4WSEY8HCBUJ6FOGDLIXP3QM5RTVKNAWZEHOBCYS)
⁃ Private Message: enter phone number, enter message, choose image, send button; enter pin; display message ( (phone number) will be notified when their message has been created)
⁃ Buy Cryptocurrency: drop drown menu of cryptocurrency to purchase (Bitcoin/Ethereum/Stellar/ZORBS), Amount in USD field, amount in chosen cryptocurrency displayed, frequency drop down menu (once/daily/weekly/monthly), buy button; enter card information (name, card number, expiration date, cvv, billing address, zip code), confirm buy button, transactions will appear on your billing statement as VEXTARO; enter pin screen; display message (You will be notified when your coin is received)
⁃ NFTs: upload image, title, description, link media, create NFT button; enter pin screen; display message (You will be notified when your NFT is created)
⁃ Earn: display message (Earn cryptocurrency doing what you do everyday, coming soon)
⁃ Files/Vault: display message (Storage for your photos, documents and more, coming soon)
⁃ Wealth: display message (Build wealth by working with a financial professional to get you to the next level), check box (I would like a financial professional to contact me about building wealth), contact me button; display message (A financial professional will contact you to achieve your financial goals)
⁃ Education: display message (Learn more about everything, coming soon)
⁃ News: display message (News from around the world, coming soon)
⁃ FAQs: use FAQs from this link https://vextaro.example/faq
⁃ Contact Us: enter message, send button; display message (Thank you for reaching out. We will reply to your message in the order it was received. Your patience is appreciated. Blessings.)

Requirements
Must have
• Application home page that looks like the Home Screen of a mobile phone
Nice to have
• Colorful icons

```html
<!DOCTYPE html>
<html lang="en">
<head>
<meta charset="utf-8">
<title>PorlenPurse Apps</title>
<link href="https://fonts.googleapis.com/css2?family=Ubuntu:wght@500;700&family=Catamaran:wght@400;500&display=swap" rel="stylesheet">
<style>
  :root {
    --page-bg: #1c3554;
    --screen-deep: #281a4c;
    --screen-light: #25196a;
    --tile: #25d4e2;
    --tile-shade: #1fb9cc;
    --ink: #ffffff;
    --ink-soft: #e6e4f2;
    --accent: #2fd9ea;
    --field: #2f2a62;
    --field-dark: #241d4e;
  }
  * { box-sizing: border-box; margin: 0; padding: 0; }
  html, body {
    width: 1200px; height: 775px; overflow: hidden;
    background: var(--page-bg);
  }
  .app-screen {
    position: absolute; left: 428px; top: 18px;
    width: 344px; height: 740px;
    border-radius: 42px;
    overflow: hidden;
    background:
      linear-gradient(122deg, transparent 0 54%, var(--screen-light) 54.2% 100%),
      var(--screen-deep);
    font-family: "Catamaran", "Hind", sans-serif;
    color: var(--ink);
  }
  .app-title {
    position: absolute; top: 58px; left: 0; width: 100%;
    text-align: center;
    font-family: "Ubuntu", sans-serif; font-weight: 700;
    font-size: 17px; letter-spacing: 0.2px;
    color: var(--ink);
  }
  .search-bar {
    position: absolute; left: 14px; top: 116px;
    width: 121px; height: 30px;
    background: var(--field); border-radius: 2px;
    display: flex; align-items: center; justify-content: space-between;
    padding: 0 10px 0 11px;
    font-size: 11px; color: var(--ink-soft);
  }
  .search-bar svg { width: 11px; height: 11px; }
  .price-ticker {
    position: absolute; left: 222px; top: 116px;
    width: 105px; height: 30px;
    background: var(--field-dark); border-radius: 2px;
    display: flex; align-items: center; justify-content: space-between;
    padding: 0 9px 0 10px;
    font-size: 11px; color: var(--ink-soft);
  }
  .price-ticker svg { width: 9px; height: 9px; }
  .price-ticker .price { color: var(--accent); }
  .app-grid {
    position: absolute; left: 0; top: 0; width: 100%; height: 100%;
    list-style: none;
  }
  .app-icon {
    position: absolute; width: 84px; margin-left: -12px;
    text-align: center;
  }
  .app-tile {
    width: 59px; height: 59px; margin: 0 auto;
    border-radius: 6px;
    background: linear-gradient(135deg, var(--tile) 0 55%, var(--tile-shade) 100%);
    display: flex; align-items: center; justify-content: center;
    box-shadow: 0 2px 4px rgba(0,0,0,0.25);
  }
  .app-tile svg {
    width: 34px; height: 34px;
    fill: none; stroke: var(--ink); stroke-width: 1.6;
    stroke-linecap: round; stroke-linejoin: round;
  }
  .app-label {
    display: block; margin-top: 8px;
    font-size: 11px; line-height: 12px; color: var(--ink-soft);
  }
  .c1 { left: 16px; } .c2 { left: 100px; } .c3 { left: 184px; } .c4 { left: 269px; }
  .r1 { top: 194px; } .r2 { top: 315px; } .r3 { top: 438px; } .r4 { top: 547px; }
</style>
</head>
<body>
<main class="app-screen">
  <h1 class="app-title">PORLENPURSE</h1>

  <div class="search-bar">
    <span>Search</span>
    <svg viewBox="0 0 12 12"><circle cx="5" cy="5" r="3.6" fill="none" stroke="#fff" stroke-width="1.8"/><path d="M7.7 7.7L11 11" stroke="#fff" stroke-width="2" stroke-linecap="round"/></svg>
  </div>

  <div class="price-ticker">
    <span>ZORBS</span>
    <svg viewBox="0 0 10 10"><path d="M1.5 7L5 3.5 8.5 7" fill="none" stroke="#fff" stroke-width="1.5"/></svg>
    <span class="price">$ 1.75</span>
  </div>

  <ul class="app-grid">
    <li class="app-icon c1 r1"><div class="app-tile"><svg viewBox="0 0 24 24"><path d="M5 8l9-3 1 3"/><rect x="4" y="8" width="15" height="11" rx="1.5"/><path d="M19 11h-4a2 2 0 0 0 0 4h4"/></svg></div><span class="app-label">Balances</span></li>
    <li class="app-icon c2 r1"><div class="app-tile"><svg viewBox="0 0 24 24"><circle cx="12" cy="12" r="8"/><path d="M8 10h8l-2-2M16 14H8l2 2"/></svg></div><span class="app-label">Transactions</span></li>
    <li class="app-icon c3 r1"><div class="app-tile"><svg viewBox="0 0 24 24"><rect x="4" y="9" width="15" height="10" rx="1.5"/><path d="M19 12h-3a1.5 1.5 0 0 0 0 3h3M12 11V3M9.5 5.5L12 3l2.5 2.5"/></svg></div><span class="app-label">Send Money</span></li>
    <li class="app-icon c4 r1"><div class="app-tile"><svg viewBox="0 0 24 24"><circle cx="11" cy="8" r="3.5"/><path d="M4 20c0-4 3-6.5 7-6.5 1.3 0 2.4.3 3.4.8M17 15v6M14 18h6"/></svg></div><span class="app-label">Create<br>Account</span></li>

    <li class="app-icon c1 r2"><div class="app-tile"><svg viewBox="0 0 24 24"><path d="M12 18s-5-5.5-5-9a5 5 0 0 1 10 0c0 3.5-5 9-5 9z"/><circle cx="12" cy="9" r="2"/><path d="M8 17.5c-2 .4-3 1-3 1.6 0 1 3 1.9 7 1.9s7-.9 7-1.9c0-.6-1-1.2-3-1.6"/></svg></div><span class="app-label">My Wallet<br>Address</span></li>
    <li class="app-icon c2 r2"><div class="app-tile"><svg viewBox="0 0 24 24"><path d="M12 4.5A7.5 7.5 0 1 1 6 17l-2.5 1.5.8-3.2A7.5 7.5 0 0 1 12 4.5z"/><rect x="9" y="11" width="6" height="4.5" rx=".8"/><path d="M10.3 11V9.5a1.7 1.7 0 0 1 3.4 0V11"/></svg></div><span class="app-label">Private<br>Message</span></li>
    <li class="app-icon c3 r2"><div class="app-tile"><svg viewBox="0 0 24 24"><circle cx="9.5" cy="14" r="5.5"/><path d="M13 5.3a5.5 5.5 0 1 1 3 9.5"/><path d="M8.5 11.5v5M8.5 11.5h2a1.2 1.2 0 0 1 0 2.4h-2h2.3a1.3 1.3 0 0 1 0 2.6H8.5M16.5 6.5v5M17.8 7.3h-2a.9.9 0 0 0 0 1.7h1.5a.9.9 0 0 1 0 1.8h-2"/></svg></div><span class="app-label">Buy<br>Cryptocurrency</span></li>
    <li class="app-icon c4 r2"><div class="app-tile"><svg viewBox="0 0 24 24"><path d="M12 3.5l7.5 4.3v8.4L12 20.5l-7.5-4.3V7.8z"/><path d="M7.6 14v-4l2.2 4v-4M11.3 14v-4h2M11.3 12h1.6M14.6 10h2.6M15.9 10v4" stroke-width="1.3"/></svg></div><span class="app-label">NFTs</span></li>

    <li class="app-icon c1 r3"><div class="app-tile"><svg viewBox="0 0 24 24"><circle cx="15" cy="7" r="3.5"/><path d="M15 5.2v3.6M3 13h3v6H3zM6 14h4l3 1.5h3a1.3 1.3 0 0 1 0 2.6h-4M6 18.5l4 1.5 9-3.5a1.3 1.3 0 0 0-1-2.4l-2 .8"/></svg></div><span class="app-label">Earn</span></li>
    <li class="app-icon c2 r3"><div class="app-tile"><svg viewBox="0 0 24 24"><path d="M3.5 9h5l1.5 1.5h7V19h-13.5z"/><path d="M6 9V6.5h4l1.5 1.5h7.5v8.5h-2.5M8.5 6.5V4h4L14 5.5h7V14h-2"/></svg></div><span class="app-label">Files/Vault</span></li>
    <li class="app-icon c3 r3"><div class="app-tile"><svg viewBox="0 0 24 24"><path d="M5 12a7 5.5 0 0 1 12-3.5l2.5-.8-.6 3a5 5 0 0 1 .6 2.3H21v3h-2a6 6 0 0 1-2 2V20h-3v-1.3h-4V20H7v-2.3A5.5 5.5 0 0 1 5 12z"/><circle cx="12" cy="5" r="2"/></svg></div><span class="app-label">Wealth</span></li>
    <li class="app-icon c4 r3"><div class="app-tile"><svg viewBox="0 0 24 24"><path d="M12 7c-2-1.5-5-2-8-1.5v12c3-.5 6 0 8 1.5 2-1.5 5-2 8-1.5v-12c-3-.5-6 0-8 1.5zM12 7v12M2.5 7.5V19.5c3.5-.5 7 0 9.5 1 2.5-1 6-1.5 9.5-1V7.5"/></svg></div><span class="app-label">Education</span></li>

    <li class="app-icon c1 r4"><div class="app-tile"><svg viewBox="0 0 24 24"><rect x="4" y="4" width="14" height="16" rx="1"/><path d="M18 8h2v10.5a1.5 1.5 0 0 1-3 0M6.5 7h9M6.5 10h4v4h-4zM12.5 10.5h3M12.5 13h3M6.5 16.5h9"/></svg></div><span class="app-label">News</span></li>
    <li class="app-icon c2 r4"><div class="app-tile"><svg viewBox="0 0 24 24"><circle cx="12" cy="12" r="8"/><path d="M9.5 9.5a2.5 2.5 0 1 1 3.5 2.3c-.7.3-1 .8-1 1.5v.7M12 16.5v.2"/></svg></div><span class="app-label">FAQs</span></li>
    <li class="app-icon c3 r4"><div class="app-tile"><svg viewBox="0 0 24 24"><path d="M6.5 4l3 .5 1.2 4-2 1.8a11 11 0 0 0 5 5l1.8-2 4 1.2.5 3c-1 1.5-3 2-4.5 1.5A15 15 0 0 1 5 8.5C4.5 7 5 5 6.5 4z"/></svg></div><span class="app-label">Contact Us</span></li>
  </ul>
</main>
</body>
</html>
```